KRV Business Card

Looking for a business card for my restaurant group I own. Four different concepts:

Copperfield Alehouse
Bristow Alehouse
Tanager's Stone Hearth Kitchen
Pellston Patty Company

Card doesn't need to include all the logos.

```html
<!DOCTYPE html>
<html lang="en">
<head>
<meta charset="utf-8">
<title>KRV Business Card</title>
<link rel="stylesheet" href="https://fonts.googleapis.com/css2?family=Poppins:wght@400;500;600&display=swap">
<style>
  :root {
    --backdrop: #2a2a2c;
    --card-black: #1c1d1f;
    --card-white: #ffffff;
    --gold: #c9a55b;
    --ink: #3b3b3d;
    --silver: #c8c8ca;
  }
  * { margin: 0; padding: 0; box-sizing: border-box; }
  html, body { width: 1200px; height: 874px; overflow: hidden; }
  body {
    background: var(--backdrop);
    font-family: "Poppins", sans-serif;
    position: relative;
  }
  .card {
    position: absolute;
    left: 270px;
    width: 660px;
    height: 377px;
    box-shadow: 0 10px 30px rgba(0,0,0,.45);
  }
  .card-back {
    top: 40px;
    background: var(--card-black);
    display: flex;
    align-items: center;
    justify-content: center;
  }
  .back-name {
    font-family: "Poppins", sans-serif;
    font-weight: 500;
    font-size: 150px;
    letter-spacing: 6px;
    color: var(--silver);
  }
  .card-front {
    top: 457px;
    background: var(--card-white);
    overflow: hidden;
  }
  .brand {
    position: absolute;
    left: 70px;
    top: 48px;
    color: var(--gold);
    font-weight: 500;
    text-transform: uppercase;
    line-height: 1.15;
  }
  .brand-initials { font-size: 46px; letter-spacing: 4px; }
  .brand-name { font-size: 21px; letter-spacing: 4px; }
  .person {
    position: absolute;
    left: 70px;
    top: 196px;
  }
  .person-name {
    color: var(--gold);
    font-weight: 600;
    font-size: 25px;
    line-height: 1.1;
  }
  .person-title {
    color: var(--ink);
    font-size: 16px;
    margin-top: 2px;
  }
  .rule {
    position: absolute;
    height: 3px;
    background: var(--gold);
  }
  .rule-left { left: 0; top: 300px; width: 372px; }
  .rule-right { left: 628px; top: 300px; width: 32px; }
  .contact {
    position: absolute;
    left: 388px;
    top: 170px;
    color: var(--ink);
    font-size: 15px;
    line-height: 1.4;
  }
  .contact p + p.group { margin-top: 10px; }
  .website {
    position: absolute;
    left: 388px;
    top: 289px;
    width: 236px;
    color: var(--ink);
    font-weight: 600;
    font-size: 13px;
    white-space: nowrap;
  }
</style>
</head>
<body>
  <section class="card card-back">
    <span class="back-name">KRV</span>
  </section>

  <section class="card card-front">
    <div class="brand">
      <div class="brand-initials">KRV</div>
      <div class="brand-name">Kestrel Ridge<br>Ventures</div>
    </div>

    <div class="person">
      <div class="person-name">Daniel Hartley</div>
      <div class="person-title">President</div>
    </div>

    <div class="contact">
      <p>2146 Alder Bend Road<br>Juneau, Alaska 99801</p>
      <p class="group">555-214-7730<br>555-318-6042<br>name@kestrelridgeventures.com</p>
    </div>

    <div class="rule rule-left"></div>
    <div class="website">www.kestrelridgeventures.com</div>
    <div class="rule rule-right"></div>
  </section>
</body>
</html>
```